KRV Business Card

Looking for a business card for my restaurant group I own. Four different concepts:

Copperfield Alehouse
Bristow Alehouse
Tanager's Stone Hearth Kitchen
Pellston Patty Company

Card doesn't need to include all the logos.

```html
<!DOCTYPE html>
<html lang="en">
<head>
<meta charset="utf-8">
<title>KRV Business Card</title>
<link rel="stylesheet" href="https://fonts.googleapis.com/css2?family=Open+Sans:wght@400;600&display=swap">
<style>
  :root {
    --page-bg: #ebebeb;
    --card-bg: #1b1a1b;
    --gold: #c9ae6f;
    --ink-light: #f2f2f2;
  }
  * { margin: 0; padding: 0; box-sizing: border-box; }
  html, body {
    width: 1200px; height: 800px; overflow: hidden;
    background: var(--page-bg);
    font-family: "Open Sans", Arial, sans-serif;
  }
  .card {
    position: absolute;
    left: 316px;
    width: 570px;
    height: 330px;
    background: var(--card-bg);
    border-radius: 24px;
    overflow: hidden;
  }
  .card--front { top: 50px; }
  .card--back { top: 419px; }

  .front__tab {
    position: absolute; left: 0; top: 45px;
    width: 12px; height: 42px;
    background: var(--gold);
    border-radius: 0 6px 6px 0;
  }
  .front__name {
    position: absolute; left: 31px; top: 40px;
    font-size: 20px; font-weight: 600; color: var(--gold);
    line-height: 24px;
  }
  .front__company {
    position: absolute; left: 31px; top: 67px;
    font-size: 15px; font-weight: 400; color: var(--ink-light);
    line-height: 20px;
  }
  .contact-list {
    position: absolute; left: 30px; top: 231px;
    list-style: none;
  }
  .contact-list li {
    display: flex; align-items: center;
    height: 20.5px;
    font-size: 14.5px; line-height: 20px; color: var(--ink-light);
  }
  .contact-list svg {
    width: 11px; height: 11px; margin-right: 10px; flex: none;
    fill: var(--gold);
  }
  .brand-name {
    color: var(--gold);
    font-weight: 600;
    text-align: center;
    letter-spacing: 0.14em;
    text-transform: uppercase;
    line-height: 1.2;
    white-space: nowrap;
  }
  .front__brand {
    position: absolute; right: 28px; top: 232px;
    width: 200px; font-size: 14px;
  }
  .back__brand {
    position: absolute; left: 0; right: 0; top: 128px;
    font-size: 30px;
  }
  .back__band {
    position: absolute; left: 0; right: 0; bottom: 0;
    height: 14px; background: var(--gold);
  }
</style>
</head>
<body>
  <section class="card card--front">
    <div class="front__tab"></div>
    <p class="front__name">Dana Orwell</p>
    <p class="front__company">Kerrville Hospitality Group</p>
    <ul class="contact-list">
      <li>
        <svg viewBox="0 0 16 16" aria-hidden="true"><path d="M3.5 1l3 3-1.8 1.8c.9 2 2.5 3.6 4.5 4.5L11 8.5l3 3-2 2.5C6.5 13.5 2.5 9.5 1 3.5z"/></svg>
        555-014-2290
      </li>
      <li>
        <svg viewBox="0 0 16 16" aria-hidden="true"><path d="M1 3h14v10H1z M2.5 4.5v.4L8 8.6l5.5-3.7v-.4z" fill-rule="evenodd"/></svg>
        dana@krvrestaurants.com
      </li>
      <li>
        <svg viewBox="0 0 16 16" aria-hidden="true"><circle cx="8" cy="8" r="7"/></svg>
        www.krvrestaurants.com
      </li>
    </ul>
    <p class="brand-name front__brand">Kerrville<br>Hospitality Group</p>
  </section>

  <section class="card card--back">
    <p class="brand-name back__brand">Kerrville<br>Hospitality Group</p>
    <div class="back__band"></div>
  </section>
</body>
</html>
```